web page look and feel - B2B enterprise application

We have an enterprise application with 10 to 15 core pages and several supporting pages or popups. To start, we want the graphical design of the Users, Roles and Data Source pages and their supporting popups, wizards, etc. to be made beautiful. That is around 10 pages in total. There is a fair amount of redundancy among the pages. I have attached 5 screenshots. We very much want the pages to project a premium feel. That is absolutely essential. The color scheme is blue and sometimes yellow (only if it makes the page look better) plus black, gray and white. If the design of these screens goes well, we would expand the project to continue with other pages. The core of what we are looking for is graphic in nature but we are open to workflow suggestions if you have them. The Roles screen needs some improvements to the layout. I am looking for everything that includes icons, fonts, spacing, etc. I assume getting to the final design will take some back and forth with multiple revisions.

Target Market(s)

Large Enterprises

Number of Pages Required

5+ page

Requirements
Must have
• Premium feel

```html
<!DOCTYPE html>
<html lang="en">
<head>
<meta charset="utf-8">
<title>Users – Norvale Data</title>
<link href="https://fonts.googleapis.com/css2?family=Exo+2:wght@300;400;500;600&family=Montserrat:wght@400&display=swap" rel="stylesheet">
<style>
:root{
  --navy:#0b1e38;
  --navy-band:#1a3556;
  --brand:#1f86ee;
  --brand-deep:#0a2d86;
  --accent:#2b8ef0;
  --accent-soft:#6cb0f2;
  --page:#e6f0fb;
  --line:#bcd8f5;
  --row-alt:#f3f3f3;
  --text:#4a4f57;
  --title:#3c4350;
  --white:#ffffff;
  --ok:#1ccf8f;
  --warn:#f5c518;
  --muted:#a9c8ec;
}
*{margin:0;padding:0;box-sizing:border-box}
html,body{width:1200px;height:786px;overflow:hidden}
body{font-family:"Exo 2",sans-serif;background:var(--page);color:var(--text);position:relative}
svg{display:block}

.topbar{position:absolute;left:0;top:0;width:1200px;height:80px;background:linear-gradient(90deg,#0b6fe0 0%,#0a52c0 45%,var(--brand-deep) 100%)}
.brand{position:absolute;left:0;top:0;width:300px;height:80px;background:linear-gradient(90deg,#1d8cf2,#0f72e2);display:flex;align-items:center;padding-left:44px;gap:10px}
.brand-dot{width:22px;height:22px;border-radius:50%;background:var(--white)}
.brand-name{color:var(--white);font-size:26px;font-weight:500;letter-spacing:-.3px}
.menu-toggle{position:absolute;left:330px;top:31px}
.tools{position:absolute;left:792px;top:26px;display:flex;gap:20px;align-items:center}
.account{position:absolute;left:1043px;top:26px;display:flex;align-items:center;gap:10px;color:var(--white);font-size:17px;font-weight:500}

.sidebar{position:absolute;left:0;top:80px;width:300px;height:706px;background:var(--navy);color:#e8eef6}
.profile{position:absolute;left:40px;top:20px;display:flex;gap:10px}
.avatar{width:40px;height:40px;border-radius:50%;background:radial-gradient(circle at 50% 40%,#c89a7c,#6b4a3a 70%);border:2px solid #e8e8e8}
.profile-name{font-size:16px;font-weight:500;margin-top:-1px}
.profile-mail{font-size:13px;color:#b9c3cf;font-weight:300;margin-top:2px}
.sidebar-rule{position:absolute;left:20px;top:80px;width:260px;height:1px;background:#34475f}
.nav-item{position:absolute;left:20px;width:280px;height:32px;display:flex;align-items:center;gap:12px;padding-left:18px;font-size:15px}
.nav-item.open{background:var(--navy-band);border-right:5px solid var(--accent)}
.nav-item .chev{position:absolute;right:32px;top:11px}
.nav-sub{padding-left:44px;gap:8px;font-size:14.5px}
.sidebar-foot{position:absolute;top:578px;left:30px;width:240px;display:flex;justify-content:space-between;font-size:14px;font-weight:500}
.sidebar-foot span{display:flex;align-items:center;gap:10px}

.page-title{position:absolute;left:329px;top:115px;font-family:Montserrat,sans-serif;font-size:31px;color:var(--title);font-weight:400}
.search{position:absolute;left:1091px;top:100px;display:flex;gap:8px;align-items:center;color:var(--accent-soft);font-size:16px}
.add-btn{position:absolute;left:1105px;top:141px;width:64px;height:27px;background:var(--accent);border-radius:2px;color:var(--white);font-size:16px;display:flex;align-items:center;justify-content:center;gap:5px}

.grid{position:absolute;left:330px;width:840px;border:1px solid var(--line)}
.row{display:grid;grid-template-columns:40px 137px 137px 137px 137px 137px 114px;height:39px;background:var(--white);font-size:15px;font-weight:300}
.row>div{display:flex;align-items:center;justify-content:center;border-left:1px solid var(--line)}
.row>div:first-child{border-left:none}
.row+.row,.detail{border-top:1px solid var(--line)}
.row.alt{background:var(--row-alt)}
.row.head{background:var(--accent);color:var(--white);font-size:16px;font-weight:400}
.row.head>div{border-color:#9fcbf6}
.actions{gap:9px}
.act{width:20px;height:20px;background:var(--accent);border-radius:2px;display:flex;align-items:center;justify-content:center}
.detail{display:grid;grid-template-columns:419px 420px;height:39px;font-size:15px;font-weight:300}
.detail>div{display:flex;align-items:center;justify-content:center;gap:10px;border-left:1px solid var(--line)}
.detail>div:first-child{border-left:none}
.detail.head{background:var(--accent);color:var(--white);font-weight:400}
.detail.head>div{border-color:#9fcbf6}
.detail.alt{background:var(--row-alt)}
.perm{display:flex;align-items:center;gap:5px;margin-right:12px}
.edit-bar{height:39px;background:var(--accent-soft);color:var(--white);font-weight:600;font-size:15px;display:flex;align-items:center;justify-content:center;border-top:1px solid var(--line)}

.pager{position:absolute;left:676px;top:732px;display:flex;align-items:center;gap:6px;color:var(--muted);font-size:15px}
.pager .current{color:var(--accent)}
.page-size{margin-left:16px;background:var(--muted);color:var(--white);font-weight:600;padding:0 5px;height:17px;display:flex;align-items:center;gap:3px}
</style>
</head>
<body>

<header class="topbar">
  <div class="brand"><span class="brand-dot"></span><span class="brand-name">Norvale Data</span></div>
  <svg class="menu-toggle" width="18" height="16" viewBox="0 0 18 16"><path d="M0 2h18M0 8h18M0 14h18" stroke="#fff" stroke-width="2.6"/></svg>
  <div class="tools">
    <svg width="28" height="28" viewBox="0 0 28 28" fill="none" stroke="#fff" stroke-width="2.4" stroke-linecap="round"><path d="M4 20a10 10 0 0 1 20 0"/><path d="M14 19l5-6"/></svg>
    <svg width="28" height="28" viewBox="0 0 28 28" fill="none" stroke="#fff" stroke-width="2.4" stroke-linecap="round"><path d="M5 24L19 10"/><path d="M22 3v4M20 5h4M14 4v2M24 12v2"/></svg>
    <svg width="30" height="30" viewBox="0 0 30 30"><circle cx="14" cy="14" r="12" fill="#c8d6ee"/><text x="14" y="20" text-anchor="middle" font-family="Exo 2,sans-serif" font-weight="700" font-size="17" fill="#1a4aa8">?</text></svg>
    <svg width="32" height="28" viewBox="0 0 32 28" fill="#fff"><circle cx="11" cy="11" r="7"/><circle cx="11" cy="11" r="3" fill="#0a52c0"/><circle cx="19" cy="21" r="5"/><circle cx="19" cy="21" r="2" fill="#0a52c0"/><circle cx="25" cy="9" r="4" fill="var(--warn)"/></svg>
  </div>
  <div class="account">
    <svg width="22" height="26" viewBox="0 0 22 26" fill="#fff"><circle cx="11" cy="7" r="6"/><path d="M1 26v-4a7 7 0 0 1 7-7h6a7 7 0 0 1 7 7v4z"/></svg>
    <span>Dana Wells</span>
    <svg width="12" height="8" viewBox="0 0 12 8" style="margin-left:12px"><path d="M1 1l5 5 5-5" stroke="#fff" stroke-width="1.6" fill="none"/></svg>
  </div>
</header>

<nav class="sidebar">
  <div class="profile">
    <div class="avatar" role="img" aria-label="Portrait photo of the signed-in user"></div>
    <div><div class="profile-name">Dana Wells</div><div class="profile-mail">dana.wells@norvale.example</div></div>
  </div>
  <div class="sidebar-rule"></div>

  <div class="nav-item open" style="top:96px">
    <svg width="16" height="18" viewBox="0 0 16 18" fill="var(--accent)"><circle cx="8" cy="5" r="4.5"/><path d="M0 18v-3a5 5 0 0 1 5-5h6a5 5 0 0 1 5 5v3z"/></svg>User
    <svg class="chev" width="11" height="7" viewBox="0 0 11 7"><path d="M1 1l4.5 4.5L10 1" stroke="#e8eef6" stroke-width="1.4" fill="none"/></svg>
  </div>
  <div class="nav-item nav-sub" style="top:128px"><svg width="18" height="18" viewBox="0 0 18 18" fill="none" stroke="#e8eef6" stroke-width="1.3"><circle cx="9" cy="5.5" r="4"/><path d="M2 17v-2a5 5 0 0 1 5-5h4a5 5 0 0 1 5 5v2z"/></svg>Roles</div>
  <div class="nav-item nav-sub" style="top:160px"><svg width="18" height="18" viewBox="0 0 18 18" fill="none" stroke="#e8eef6" stroke-width="1.3"><path d="M4 13V8a5 5 0 0 1 10 0v5l2 2H2z"/><path d="M7 16a2 2 0 0 0 4 0"/></svg>Notification Groups</div>

  <div class="nav-item open" style="top:192px">
    <svg width="18" height="16" viewBox="0 0 18 16" fill="var(--accent)"><rect width="18" height="4.5"/><rect y="5.8" width="18" height="4.5"/><rect y="11.6" width="18" height="4.4"/></svg>Data Source
    <svg class="chev" width="11" height="7" viewBox="0 0 11 7"><path d="M1 1l4.5 4.5L10 1" stroke="#e8eef6" stroke-width="1.4" fill="none"/></svg>
  </div>
  <div class="nav-item nav-sub" style="top:224px"><svg width="18" height="16" viewBox="0 0 18 16" fill="none" stroke="#e8eef6" stroke-width="1.3"><path d="M7 1h10v14H7"/><path d="M1 8h10M8 5l3 3-3 3"/></svg>Data Object Relationship</div>
  <div class="nav-item" style="top:256px"><svg width="18" height="18" viewBox="0 0 18 18" fill="#e8eef6"><rect width="8" height="18"/><rect x="10" width="8" height="8"/><rect x="10" y="10" width="8" height="8"/></svg>Data Sets</div>
  <div class="nav-item" style="top:288px"><svg width="18" height="18" viewBox="0 0 18 18" fill="#e8eef6"><rect width="7" height="18"/><rect x="9" width="9" height="2.6"/><rect x="9" y="5" width="9" height="2.6"/><rect x="9" y="10" width="9" height="2.6"/><rect x="9" y="15" width="9" height="3"/></svg>Rule Sets</div>
  <div class="nav-item" style="top:320px"><svg width="18" height="18" viewBox="0 0 18 18" fill="none" stroke="#e8eef6" stroke-width="1.6"><circle cx="9" cy="9" r="8"/><path d="M9 4v5l3 2"/></svg>Schedule</div>
  <div class="nav-item open" style="top:352px">
    <svg width="18" height="18" viewBox="0 0 18 18" fill="none" stroke="var(--accent)" stroke-width="1.8"><path d="M3 8a6 6 0 0 1 11-3M15 10a6 6 0 0 1-11 3"/><path d="M14 1v4h-4M4 17v-4h4"/></svg>Metadata Import/Export
    <svg class="chev" width="11" height="7" viewBox="0 0 11 7"><path d="M1 1l4.5 4.5L10 1" stroke="#e8eef6" stroke-width="1.4" fill="none"/></svg>
  </div>
  <div class="nav-item nav-sub" style="top:384px"><svg width="14" height="16" viewBox="0 0 14 16" fill="none" stroke="#e8eef6" stroke-width="1.4"><path d="M7 1v14M2 10l5 5 5-5"/></svg>Import</div>
  <div class="nav-item nav-sub" style="top:416px"><svg width="14" height="16" viewBox="0 0 14 16" fill="none" stroke="#e8eef6" stroke-width="1.4"><path d="M7 15V1M2 6l5-5 5 5"/></svg>Export</div>

  <div class="sidebar-foot">
    <span><svg width="24" height="26" viewBox="0 0 24 26" fill="none" stroke="#fff" stroke-width="2"><rect x="1" y="4" width="22" height="21" rx="2"/><path d="M1 10h22M6 1v5M18 1v5"/><text x="12" y="23" text-anchor="middle" font-family="Exo 2,sans-serif" font-size="11" font-weight="700" fill="#fff" stroke="none">5</text></svg>July 05</span>
    <span><svg width="26" height="26" viewBox="0 0 26 26" fill="none" stroke="#fff" stroke-width="2"><circle cx="13" cy="13" r="11.5"/><path d="M13 6v7l4 3"/></svg>18:36</span>
  </div>
</nav>

<main>
  <h1 class="page-title">Users</h1>
  <div class="search">Search <svg width="22" height="22" viewBox="0 0 22 22" fill="none" stroke="var(--accent-soft)" stroke-width="1.8"><circle cx="9" cy="9" r="7.5"/><path d="M14.5 14.5l6 6"/></svg></div>
  <div class="add-btn"><svg width="16" height="16" viewBox="0 0 16 16" fill="none" stroke="#fff" stroke-width="1.4"><circle cx="8" cy="8" r="7"/><path d="M8 4.5v7M4.5 8h7"/></svg>Add</div>

  <section class="grid" style="top:188px">
    <div class="row head"><div></div><div>First Name</div><div>Last Name</div><div>Username</div><div>Email</div><div>Status</div><div>Edit</div></div>
    <div class="row">
      <div><svg width="8" height="11" viewBox="0 0 8 11"><path d="M1.5 1l5 4.5-5 4.5" stroke="var(--accent)" stroke-width="1.8" fill="none"/></svg></div>
      <div>Test</div><div>Test</div><div>test.1</div><div>test@test.com</div><div>Active</div>
      <div class="actions">
        <span class="act"><svg width="12" height="12" viewBox="0 0 12 12" fill="none" stroke="#fff" stroke-width="1.3"><path d="M2 9l6.5-6.5 1.5 1.5L3.5 10.5H2zM1 11.5h10"/></svg></span>
        <span class="act"><svg width="12" height="12" viewBox="0 0 12 12" fill="none" stroke="#fff" stroke-width="1.3"><rect x="3.5" y="3.5" width="7" height="7.5" rx="1"/><path d="M2 8.5V2a1 1 0 0 1 1-1h5"/></svg></span>
        <span class="act"><svg width="12" height="12" viewBox="0 0 12 12" fill="none" stroke="#fff" stroke-width="1.3"><path d="M1 3h10M4.5 3V1.5h3V3M2.5 3l.7 8h5.6l.7-8M5 5v4M7 5v4"/></svg></span>
      </div>
    </div>
    <div class="detail head"><div>Object</div><div>Permissions</div></div>
    <div class="detail"><div>System Settings</div><div>
      <span class="perm"><svg width="20" height="20" viewBox="0 0 20 20"><circle cx="10" cy="10" r="10" fill="var(--ok)"/><path d="M5.5 10.2l3 3 6-6" stroke="#fff" stroke-width="2.2" fill="none"/></svg>Read</span>
      <span class="perm"><svg width="20" height="20" viewBox="0 0 20 20"><circle cx="10" cy="10" r="10" fill="var(--ok)"/><path d="M5.5 10.2l3 3 6-6" stroke="#fff" stroke-width="2.2" fill="none"/></svg>Write</span>
    </div></div>
    <div class="detail alt"><div>Users</div><div>
      <span class="perm"><svg width="20" height="20" viewBox="0 0 20 20"><circle cx="10" cy="10" r="10" fill="var(--ok)"/><path d="M5.5 10.2l3 3 6-6" stroke="#fff" stroke-width="2.2" fill="none"/></svg>Read</span>
      <span class="perm"><svg width="20" height="20" viewBox="0 0 20 20"><circle cx="10" cy="10" r="10" fill="var(--ok)"/><path d="M5.5 10.2l3 3 6-6" stroke="#fff" stroke-width="2.2" fill="none"/></svg>Write</span>
    </div></div>
    <div class="detail head"><div>Data Source</div><div>Role</div></div>
    <div class="detail"><div>All Data Sources</div><div>All Administrator</div></div>
    <div class="edit-bar">Edit</div>
  </section>

  <section class="grid" style="top:511px">
    <div class="row"><div><svg width="11" height="8" viewBox="0 0 11 8"><path d="M1 1.5l4.5 5 4.5-5" stroke="var(--accent)" stroke-width="1.8" fill="none"/></svg></div><div>Test</div><div>Test</div><div>test.1</div><div>test@test.com</div><div>Active</div><div class="actions"><span class="act"><svg width="12" height="12" viewBox="0 0 12 12" fill="none" stroke="#fff" stroke-width="1.3"><path d="M2 9l6.5-6.5 1.5 1.5L3.5 10.5H2zM1 11.5h10"/></svg></span><span class="act"><svg width="12" height="12" viewBox="0 0 12 12" fill="none" stroke="#fff" stroke-width="1.3"><rect x="3.5" y="3.5" width="7" height="7.5" rx="1"/><path d="M2 8.5V2a1 1 0 0 1 1-1h5"/></svg></span><span class="act"><svg width="12" height="12" viewBox="0 0 12 12" fill="none" stroke="#fff" stroke-width="1.3"><path d="M1 3h10M4.5 3V1.5h3V3M2.5 3l.7 8h5.6l.7-8M5 5v4M7 5v4"/></svg></span></div></div>
    <div class="row alt"><div><svg width="11" height="8" viewBox="0 0 11 8"><path d="M1 1.5l4.5 5 4.5-5" stroke="var(--accent)" stroke-width="1.8" fill="none"/></svg></div><div>Test</div><div>Test</div><div>test.1</div><div>test@test.com</div><div>Active</div><div class="actions"><span class="act"><svg width="12" height="12" viewBox="0 0 12 12" fill="none" stroke="#fff" stroke-width="1.3"><path d="M2 9l6.5-6.5 1.5 1.5L3.5 10.5H2zM1 11.5h10"/></svg></span><span class="act"><svg width="12" height="12" viewBox="0 0 12 12" fill="none" stroke="#fff" stroke-width="1.3"><rect x="3.5" y="3.5" width="7" height="7.5" rx="1"/><path d="M2 8.5V2a1 1 0 0 1 1-1h5"/></svg></span><span class="act"><svg width="12" height="12" viewBox="0 0 12 12" fill="none" stroke="#fff" stroke-width="1.3"><path d="M1 3h10M4.5 3V1.5h3V3M2.5 3l.7 8h5.6l.7-8M5 5v4M7 5v4"/></svg></span></div></div>
    <div class="row"><div><svg width="11" height="8" viewBox="0 0 11 8"><path d="M1 1.5l4.5 5 4.5-5" stroke="var(--accent)" stroke-width="1.8" fill="none"/></svg></div><div>Test</div><div>Test</div><div>test.1</div><div>test@test.com</div><div>Active</div><div class="actions"><span class="act"><svg width="12" height="12" viewBox="0 0 12 12" fill="none" stroke="#fff" stroke-width="1.3"><path d="M2 9l6.5-6.5 1.5 1.5L3.5 10.5H2zM1 11.5h10"/></svg></span><span class="act"><svg width="12" height="12" viewBox="0 0 12 12" fill="none" stroke="#fff" stroke-width="1.3"><rect x="3.5" y="3.5" width="7" height="7.5" rx="1"/><path d="M2 8.5V2a1 1 0 0 1 1-1h5"/></svg></span><span class="act"><svg width="12" height="12" viewBox="0 0 12 12" fill="none" stroke="#fff" stroke-width="1.3"><path d="M1 3h10M4.5 3V1.5h3V3M2.5 3l.7 8h5.6l.7-8M5 5v4M7 5v4"/></svg></span></div></div>
    <div class="row alt"><div><svg width="11" height="8" viewBox="0 0 11 8"><path d="M1 1.5l4.5 5 4.5-5" stroke="var(--accent)" stroke-width="1.8" fill="none"/></svg></div><div>Test</div><div>Test</div><div>test.1</div><div>test@test.com</div><div>Active</div><div class="actions"><span class="act"><svg width="12" height="12" viewBox="0 0 12 12" fill="none" stroke="#fff" stroke-width="1.3"><path d="M2 9l6.5-6.5 1.5 1.5L3.5 10.5H2zM1 11.5h10"/></svg></span><span class="act"><svg width="12" height="12" viewBox="0 0 12 12" fill="none" stroke="#fff" stroke-width="1.3"><rect x="3.5" y="3.5" width="7" height="7.5" rx="1"/><path d="M2 8.5V2a1 1 0 0 1 1-1h5"/></svg></span><span class="act"><svg width="12" height="12" viewBox="0 0 12 12" fill="none" stroke="#fff" stroke-width="1.3"><path d="M1 3h10M4.5 3V1.5h3V3M2.5 3l.7 8h5.6l.7-8M5 5v4M7 5v4"/></svg></span></div></div>
    <div class="row"><div><svg width="11" height="8" viewBox="0 0 11 8"><path d="M1 1.5l4.5 5 4.5-5" stroke="var(--accent)" stroke-width="1.8" fill="none"/></svg></div><div>Test</div><div>Test</div><div>test.1</div><div>test@test.com</div><div>Active</div><div class="actions"><span class="act"><svg width="12" height="12" viewBox="0 0 12 12" fill="none" stroke="#fff" stroke-width="1.3"><path d="M2 9l6.5-6.5 1.5 1.5L3.5 10.5H2zM1 11.5h10"/></svg></span><span class="act"><svg width="12" height="12" viewBox="0 0 12 12" fill="none" stroke="#fff" stroke-width="1.3"><rect x="3.5" y="3.5" width="7" height="7.5" rx="1"/><path d="M2 8.5V2a1 1 0 0 1 1-1h5"/></svg></span><span class="act"><svg width="12" height="12" viewBox="0 0 12 12" fill="none" stroke="#fff" stroke-width="1.3"><path d="M1 3h10M4.5 3V1.5h3V3M2.5 3l.7 8h5.6l.7-8M5 5v4M7 5v4"/></svg></span></div></div>
  </section>

  <div class="pager">
    <svg width="8" height="12" viewBox="0 0 8 12"><path d="M6.5 1L1.5 6l5 5" stroke="var(--accent-soft)" stroke-width="1.8" fill="none"/></svg>
    <span class="current">1</span><span>2</span><span>3</span><span>4</span>
    <svg width="8" height="12" viewBox="0 0 8 12" style="margin-left:6px"><path d="M1.5 1l5 5-5 5" stroke="var(--accent-soft)" stroke-width="1.8" fill="none"/></svg>
    <span class="page-size">20 <svg width="7" height="5" viewBox="0 0 7 5"><path d="M1 1l2.5 2.5L6 1" stroke="#fff" stroke-width="1.2" fill="none"/></svg></span>
  </div>
</main>

</body>
</html>
```